Payment company requires web design

We need a web design for a new company based in Singapore.

The company focuses on providing 2 key products: 1) an alternative payment option (i.e. like quib or trelloquin options) on the traditional checkout process 2) a replacement/outsource of a merchants payment page. Key in the UX flow is a end customer dashboard that manages all payments.

We look to provide a simple, fluid and easy to use payment process. The dashboard is minimalistic that allows easy navigation, review of transactions and all available options through gamification.

The final design should communicate ease of use, flexibility and transparency.

Target Market(s)

The value is for the merchant - retail/travel/insurance companies. However its the merchant's end customers that are the target and who the UX is built for.

Industry/Entity Type

It Company

Logo Text

zelnar

Number of Pages Required

5+ page

Colors
ec1f27

Requirements
Must have
• 7 pages mimicking UX flow
• payment page * 2 - 1) alternative payment type 2) outsource of merchants payment page to our business
• our landing page
• end customer verification page
• end customer registration
• customer dashboard
• UX flow in attached file
Nice to have
• open to ideas
• have asked for the logo to be added
• logo to have the colour red (chinese for prosperity)
• the company is all about flexibility, transparency in personal finance management with the option of instalment payments

```html
<!DOCTYPE html>
<html lang="en">
<head>
<meta charset="utf-8">
<title>Zelnar — Flexible Payments</title>
<link href="https://fonts.googleapis.com/css2?family=Open+Sans:wght@400;500;600;700;800&display=swap" rel="stylesheet">
<style>
:root{
  --red:#ec1f27;
  --ink:#2b2b2b;
  --text:#555;
  --muted:#777;
  --band:#f2f2f2;
  --hero:#efefef;
  --line:#e2e2e2;
  --white:#fff;
}
*{margin:0;padding:0;box-sizing:border-box}
html,body{width:1200px;height:2267px;overflow:hidden}
body{font-family:"Open Sans",Arial,sans-serif;color:var(--ink);background:var(--white);position:relative}
.abs{position:absolute}
.btn{position:absolute;background:var(--red);color:var(--white);font-weight:700;text-transform:uppercase;display:flex;align-items:center;justify-content:center;border-radius:2px;box-shadow:0 2px 0 #b8141b}

/* header */
.site-header{position:absolute;left:0;top:0;width:1200px;height:91px;background:var(--white);border-top:3px solid var(--red);border-bottom:2px solid #e6e6e6}
.logo{position:absolute;left:162px;top:28px;font-size:33px;font-weight:800;color:var(--red);letter-spacing:.5px}
.nav a{position:absolute;top:40px;font-size:12px;font-weight:400;color:#333;text-decoration:none;text-transform:uppercase}
.nav a.active{color:var(--red)}
.nav-caret{position:absolute;left:484px;top:81px;width:0;height:0;border-left:8px solid transparent;border-right:8px solid transparent;border-bottom:8px solid var(--red)}
.btn-login{left:969px;top:33px;width:68px;height:32px;font-size:11px}

/* hero */
.hero{position:absolute;left:0;top:91px;width:1200px;height:503px;background:var(--hero)}
.hero-photo{position:absolute;left:489px;top:0;width:711px;height:503px;background:linear-gradient(120deg,#f4f4f2 0%,#e9e6e3 45%,#d9d4cf 100%)}
.hero-title{position:absolute;left:162px;top:139px;font-size:29px;line-height:38px;font-weight:400;color:#333}
.hero-title .accent{color:var(--red)}
.hero-copy{position:absolute;left:162px;top:265px;width:440px;font-size:14.5px;line-height:26px;color:#333}
.btn-register{left:162px;top:341px;width:126px;height:35px;font-size:14px;font-weight:600}
.slider-arrow{position:absolute;top:235px;width:32px;height:32px;border:1.5px solid #c8c8c8;border-radius:50%}

/* welcome */
.welcome-title{position:absolute;left:0;top:636px;width:1200px;text-align:center;font-size:23px;font-weight:500;color:var(--red)}
.welcome-lead{position:absolute;left:0;top:684px;width:1200px;text-align:center;font-size:16.5px;font-weight:600;color:#222}
.welcome-copy{position:absolute;left:160px;top:722px;width:880px;text-align:center;font-size:11px;line-height:19.5px;color:var(--text)}
.btn-small{height:33px;font-size:10.5px}

/* how it works */
.how{position:absolute;left:0;top:903px;width:1200px;height:431px;background:var(--band)}
.section-title{position:absolute;left:0;width:1200px;text-align:center;font-size:23px;font-weight:500;color:#333;text-transform:uppercase}
.step{position:absolute;top:140px;width:200px;text-align:center}
.step-circle{width:96px;height:96px;margin:0 auto;border-radius:50%;border:3px solid var(--red);background:linear-gradient(135deg,#d8cfc6,#9d8f85)}
.step-label{margin-top:19px;font-size:14px;font-weight:500;color:#222;text-transform:uppercase}
.step-copy{width:172px;margin:12px auto 0;font-size:11px;line-height:20px;color:var(--text)}

/* reasons */
.card{position:absolute;top:1437px;width:273px}
.card-photo{width:273px;height:150px;border:2px solid #ddd;background:linear-gradient(135deg,#6f5a52,#b79c8c 55%,#3c3537)}
.card-title{margin-top:13px;font-size:15px;font-weight:600;color:#222}
.card-copy{margin-top:10px;width:268px;font-size:10.7px;line-height:19.5px;color:var(--text)}

/* cta */
.cta{position:absolute;left:0;top:1803px;width:1200px;height:207px;background:var(--band)}
.cta-title{position:absolute;left:0;top:52px;width:1200px;text-align:center;font-size:23px;line-height:32px;font-weight:500;color:#333}

/* footer */
.footer-col{position:absolute;top:2071px}
.footer-col h4{font-size:12px;font-weight:600;color:#222;text-transform:uppercase;margin-bottom:17px}
.footer-col li{list-style:none;font-size:11px;line-height:21px;color:var(--text)}
.social{position:absolute;top:2116px;width:27px;height:27px;border-radius:50%}
.legal{position:absolute;left:865px;top:2176px;font-size:11px;line-height:19px;color:#222}
</style>
</head>
<body>

<header class="site-header">
  <div class="logo">ZELNAR</div>
  <nav class="nav">
    <a class="active" style="left:473px">Home</a>
    <a style="left:543px">About</a>
    <a style="left:618px">For Merchant Payment</a>
    <a style="left:799px">For Personal Payment</a>
  </nav>
  <div class="nav-caret"></div>
  <div class="btn btn-login">Log in</div>
</header>

<section class="hero">
  <div class="hero-photo" role="img" aria-label="Photo of a smiling couple at a laptop paying online with a card"></div>
  <h1 class="hero-title"><span class="accent">We are about</span><br>Flexibility Transparency in<br><span class="accent">Personal Finance Management</span></h1>
  <p class="hero-copy">Lorem ipsum dolor sit amet, consectetur adipiscing elit, sed do eiusmod tempor incididunt ut laboreloreit ansetetmmo.</p>
  <div class="btn btn-register">Register</div>
  <svg class="slider-arrow" style="left:29px" viewBox="0 0 32 32"><path d="M18 11l-5 5 5 5" fill="none" stroke="#bbb" stroke-width="1.5"/></svg>
  <svg class="slider-arrow" style="left:1139px" viewBox="0 0 32 32"><path d="M14 11l5 5-5 5" fill="none" stroke="#bbb" stroke-width="1.5"/></svg>
</section>

<section class="welcome">
  <h2 class="welcome-title">WELCOME TO ZELNAR</h2>
  <p class="welcome-lead">Lorem ipsum dolor sit amet, consectetur adipiscing elit, sed deiusm tempor incididunt ut laborelo</p>
  <p class="welcome-copy">Sed ut perspiciatis unde omnis iste natus error sit voluptatem accusantium dolore mq ue laudantium, totam rem aperiam, eaque ipsa quae ab illo inventore veritatis et quasi archit ecto beatae vitae dicta sunt explicabo. Nemo enim ipsam volupta tem quia volup tas sit aspernatur aut odit aut fugit, sed quia conse quun tur mag ni dolores eos qui rati one voluptatem sequi nesciuSed ut perspiciatis unde omnis iste natus error sit voluptatem accusantium dolore mq ue laudantium, totam rem aperiam, eaque ipsa quae ab illo inventore veritatis et quasi archit ecto beatae vitae dicta sunt explicabo. Nemo enim ipsam volupta tem quia volup tas sit aspernatur aut odit aut fugit.</p>
  <div class="btn btn-small" style="left:551px;top:822px;width:97px">Read more »</div>
</section>

<section class="how">
  <h2 class="section-title" style="top:58px">How does it work?</h2>
  <svg class="abs" style="left:0;top:0" width="1200" height="431" viewBox="0 0 1200 431">
    <g fill="none" stroke="#dcdcdc" stroke-width="6" stroke-linecap="round">
      <path d="M318 175 Q362 150 400 185"/><path d="M553 180 Q600 145 645 175"/><path d="M788 175 Q832 150 868 180"/>
    </g>
    <g fill="#dcdcdc"><path d="M392 190l16 2-6-15z"/><path d="M640 168l16 3-9 13z"/><path d="M860 185l16 2-6-15z"/></g>
  </svg>
  <div class="step" style="left:150px"><div class="step-circle" role="img" aria-label="Photo of a consumer paying by phone"></div><div class="step-label">Consumer</div><p class="step-copy">Sed ut perspiciatis unde otsrs itvoluptatem accusan tium dolore mq ue laudpta te iu dololorlo</p></div>
  <div class="step" style="left:385px"><div class="step-circle" role="img" aria-label="Photo of a card at a merchant terminal"></div><div class="step-label">Merchants</div><p class="step-copy">Sed ut perspiciatis unde otsrs itvoluptatem accusan tium dolore mq ue laudpta te iu dololorlo</p></div>
  <div class="step" style="left:621px"><div class="step-circle" role="img" aria-label="Photo of hands exchanging a payment card"></div><div class="step-label">Payments</div><p class="step-copy">Sed ut perspiciatis unde otsrs itvoluptatem accusan tium dolore mq ue laudpta te iu dololorlo</p></div>
  <div class="step" style="left:856px"><div class="step-circle" role="img" aria-label="Photo of someone reviewing receipts"></div><div class="step-label">Management</div><p class="step-copy">Sed ut perspiciatis unde otsrs itvoluptatem accusan tium dolore mq ue laudpta te iu dololorlo</p></div>
</section>

<section class="reasons">
  <h2 class="section-title" style="top:1375px">More reasons to use Zelnar</h2>
  <div class="card" style="left:162px"><div class="card-photo" role="img" aria-label="Photo of a phone tapped on a payment terminal"></div><div class="card-title">Lorem ipsum dolor sit ame</div><p class="card-copy">Sed ut p loerspiciatis unde omnis iste natus error sit volup tatem accusantium dolore mq uloe laud antium, tota m rem aperiam, eaque ipsa quae ab.</p></div>
  <div class="card" style="left:465px"><div class="card-photo" role="img" aria-label="Photo of a hand holding a card over a tablet" style="background:linear-gradient(135deg,#c9d6e2,#e8e2d8 50%,#9aa9b6)"></div><div class="card-title">Lorem ipsum dolor sit ame</div><p class="card-copy">Sed ut p loerspiciatis unde omnis iste natus error sit volup tatem accusantium dolore mq uloe laud antium, tota m rem aperiam, eaque ipsa quae ab.</p></div>
  <div class="card" style="left:768px"><div class="card-photo" role="img" aria-label="Photo of a card reader in a shop" style="background:linear-gradient(135deg,#3a4a6a,#a56a3a 55%,#2a2a2a)"></div><div class="card-title">Lorem ipsum dolor sit ame</div><p class="card-copy">Sed ut p loerspiciatis unde omnis iste natus error sit volup tatem accusantium dolore mq uloe laud antium, tota m rem aperiam, eaque ipsa quae ab.</p></div>
  <div class="btn btn-small" style="left:162px;top:1709px;width:97px">Read more »</div>
  <div class="btn btn-small" style="left:465px;top:1709px;width:97px">Read more »</div>
  <div class="btn btn-small" style="left:768px;top:1709px;width:97px">Read more »</div>
</section>

<section class="cta">
  <h2 class="cta-title">Ready to get started? Get in touch,<br>or create an account</h2>
  <div class="btn btn-small" style="left:534px;top:141px;width:134px">Create account »</div>
</section>

<footer>
  <div class="footer-col" style="left:162px"><h4>Products</h4><ul><li>Payments</li><li>Instalments</li><li>Checkout</li><li>Ledger</li><li>Wallet</li></ul></div>
  <div class="footer-col" style="left:346px"><h4>Developers</h4><ul><li>Documentation</li><li>API reference</li><li>API status</li><li>Open source</li><li>Pricing</li><li>Customers</li></ul></div>
  <div class="footer-col" style="left:536px"><h4>What we do</h4><ul><li>Sed ut perspiciatis</li><li>Qnde omnis iste n</li><li>Wtus error sit voluptat</li><li>em accusantiu</li><li>Gdoloremque</li></ul></div>
  <div class="footer-col" style="left:716px"><h4>Company</h4><ul><li>Company info</li><li>News</li><li>Investors</li><li>Sed ut perspici</li><li>em accusantiu</li></ul></div>
  <div class="footer-col" style="left:865px"><h4>Follow us</h4></div>
  <div class="social" style="left:865px;background:#5aa6d6" role="img" aria-label="Social link"></div>
  <div class="social" style="left:897px;background:#2f5ea0" role="img" aria-label="Social link"></div>
  <div class="social" style="left:929px;background:#1e6aa0" role="img" aria-label="Social link"></div>
  <div class="social" style="left:961px;background:#d6452f" role="img" aria-label="Social link"></div>
  <p class="legal">© 2016 All Copyrights are Reserved.<br>Privacy Policy &nbsp; Sitemap</p>
</footer>

</body>
</html>
```